Corporate Design - Immobilienverwaltungsgesellschaft
Zielgruppe
An- und Verkauf, Verwaltung und Vermietung von Immobilien
Zielgruppen: Immobilienspekulanten, Wohnungskäufer, Mieter, Vermieter
Aufgabenstellung
Wir suchen ein hochwertiges Design für eine in Gründung befindliche Gesellschaft mit beschränkter Haftung.
Diese wird aus 2 Gesellschaftern, Katrin und Torsten Fellmer bestehen.
Das Hauptziel der Gesellschaft wird der An- und Verkauf von Immobilien bis zu 1. Million Euro je Kaufobjekt sein
Mit dem Nachnamen der Gesellschafter kann auch gespielt werden, beispielsweise bei Abkürzungen. Die Bezeichnung F&F Verwaltungsgesellschaft mbH ist nicht zwingend, lediglich das Kürzel 'mbH' oder auch 'GmbH' ist aufgrund der Rechtsform der Gesellschaft zwingend aufzunehmen.
Diverse Designideen haben wir bereits vorliegen; hierauf kann aufgebaut werden, siehe Uploads
Unter anderem eine Anlehnung an die unter derselben Firmenadresse der Gesellschaft bestehende Rechtsanwaltskanzlei und deren Cooperate Design wäre eine Idee, jedoch keine zwingende Voraussetzung.

```html
<!DOCTYPE html>
<html lang="de">
<head>
<meta charset="utf-8">
<title>F&amp;F Verwaltungsgesellschaft mbH – Geschäftsausstattung</title>
<link href="https://fonts.googleapis.com/css2?family=Roboto+Condensed:wght@400;700&family=Raleway:wght@400&display=swap" rel="stylesheet">
<style>
  :root {
    --navy: #07035f;
    --cyan: #00c6f3;
    --stage: #e6e6e6;
    --paper: #ffffff;
    --grey-text: #8a8a8a;
    --faint: #e6e6e6;
  }
  * { margin: 0; padding: 0; box-sizing: border-box; }
  html, body { width: 1200px; height: 770px; overflow: hidden; background: var(--stage); }
  .canvas { position: relative; width: 1200px; height: 770px; background: var(--stage); font-family: "Roboto Condensed", sans-serif; }

  /* Letterhead */
  .letterhead { position: absolute; left: 93px; top: 55px; width: 456px; height: 650px; background: var(--paper); overflow: hidden; }
  .letterhead-art { position: absolute; inset: 0; width: 456px; height: 650px; }
  .letterhead-brand { position: absolute; right: 22px; top: 50px; color: var(--navy); font-weight: 700; font-size: 11px; letter-spacing: .2px; }
  .letterhead-sender { position: absolute; left: 34px; top: 114px; font-size: 8.5px; color: var(--navy); text-decoration: underline; }
  .staff-list { position: absolute; left: 334px; top: 117px; height: 383px; border-left: 1px solid var(--navy); padding-left: 6px; width: 120px; }
  .staff-member { height: 100px; }
  .staff-member h3 { font-size: 6.3px; font-weight: 700; color: var(--navy); line-height: 1.2; }
  .staff-member p { font-family: "Raleway", sans-serif; font-size: 6.2px; color: var(--grey-text); line-height: 1.45; margin-bottom: 4px; }
  .letterhead-footer { position: absolute; left: 0; bottom: 0; width: 456px; height: 30px; display: flex; align-items: center; justify-content: space-between; padding: 0 15px 0 4px; color: #fff; }
  .bank-details { font-size: 5.4px; font-weight: 700; letter-spacing: .1px; }
  .bank-details .sep { color: var(--cyan); margin: 0 6px; }
  .website { font-size: 12px; font-weight: 700; }

  /* Business cards */
  .card { position: absolute; left: 600px; width: 488px; height: 274px; display: flex; align-items: center; justify-content: center; }
  .card-light { top: 80px; background: var(--paper); color: var(--navy); }
  .card-dark { top: 415px; background: var(--navy); color: #fff; }
  .card-brand { font-weight: 700; font-size: 24px; letter-spacing: .3px; }
</style>
</head>
<body>
<main class="canvas">

  <section class="letterhead">
    <svg class="letterhead-art" viewBox="0 0 456 650" aria-hidden="true">
      <text x="-4" y="612" font-family="Roboto Condensed, sans-serif" font-weight="700" font-size="120" fill="var(--faint)">F&amp;F</text>
      <path d="M0,0 H456 V8 C300,12 130,30 0,60 Z" fill="var(--navy)"/>
      <path d="M0,60 C130,30 300,12 456,8 V14 C300,22 140,48 0,72 Z" fill="var(--cyan)"/>
      <path d="M0,562 C150,602 320,620 456,616 V650 H0 Z" fill="var(--cyan)"/>
      <path d="M0,590 C150,620 320,628 456,624 V650 H0 Z" fill="var(--navy)"/>
    </svg>

    <div class="letterhead-brand">F&amp;F Verwaltungsgesellschaft mbH</div>
    <div class="letterhead-sender">F&amp;F Verwaltungsgesellschaft mbH</div>

    <div class="staff-list">
      <article class="staff-member">
        <h3>Yourname</h3><p>Rechtsanwalt</p>
        <h3>Tätigkeitsschwerpunkte :</h3><p>Bau- und Werkvertragsrecht<br>Immobilienrecht<br>Wohnungseigentumsrecht</p>
        <h3>Interessenschwerpunkte:</h3><p>Arbeitsrecht<br>Sozialversicherungsrecht</p>
      </article>
      <article class="staff-member">
        <h3>Yourname</h3><p>Rechtsanwalt</p>
        <h3>Tätigkeitsschwerpunkte :</h3><p>Bau- und Werkvertragsrecht<br>Immobilienrecht<br>Wohnungseigentumsrecht</p>
        <h3>Interessenschwerpunkte:</h3><p>Arbeitsrecht<br>Sozialversicherungsrecht</p>
      </article>
      <article class="staff-member">
        <h3>Yourname</h3><p>Rechtsanwalt</p>
        <h3>Tätigkeitsschwerpunkte :</h3><p>Bau- und Werkvertragsrecht<br>Immobilienrecht<br>Wohnungseigentumsrecht</p>
        <h3>Interessenschwerpunkte:</h3><p>Arbeitsrecht<br>Sozialversicherungsrecht</p>
      </article>
      <article class="staff-member">
        <h3>Yourname</h3><p>Rechtsanwalt</p>
        <h3>Tätigkeitsschwerpunkte :</h3><p>Bau- und Werkvertragsrecht<br>Immobilienrecht<br>Wohnungseigentumsrecht</p>
        <h3>Interessenschwerpunkte:</h3><p>Arbeitsrecht<br>Sozialversicherungsrecht</p>
      </article>
    </div>

    <footer class="letterhead-footer">
      <div class="bank-details">Bankinstitut : Stadtbank Lindenau<span class="sep">•</span>IBAN : DE12 3456 7890 1234 5678 90<span class="sep">•</span>BIC : LINDDE12</div>
      <div class="website">www.f&amp;f.de</div>
    </footer>
  </section>

  <section class="card card-light">
    <div class="card-brand">F&amp;F Verwaltungsgesellschaft mbH</div>
  </section>

  <section class="card card-dark">
    <div class="card-brand">F&amp;F Verwaltungsgesellschaft mbH</div>
  </section>

</main>
</body>
</html>
```